HearthMile business card and stationary design

We are looking for a simple yet elegant design for our mortgage company business card and stationary.

The card should include:
Name (Marcus Pell)
Title (CEO)
Phone Number (541-555-0182)
Address (48 Birchwell Court, Suite 314, Farrow Bend, OR 97512)
Email (email@hearthmile.example)
"NMLS" i.e. (NMLS 61947)
"Company NMLS" (Company NMLS 274615)

Contact Information for Business Card

See above

```html
<!DOCTYPE html>
<html lang="en">
<head>
<meta charset="utf-8">
<title>HearthMile Business Card</title>
<link rel="stylesheet" href="https://fonts.googleapis.com/css2?family=Montserrat:wght@400;500;600&display=swap">
<style>
  :root {
    --backdrop: #6b6b6b;
    --navy: #1b2632;
    --sky: #29a9e0;
    --paper: #ffffff;
    --ink: #4a4f55;
  }
  * { margin: 0; padding: 0; box-sizing: border-box; }
  html, body {
    width: 1049px;
    height: 1200px;
    overflow: hidden;
    background: var(--backdrop);
    font-family: "Montserrat", Arial, sans-serif;
  }
  .card {
    position: absolute;
    left: 163px;
    width: 723px;
    height: 413px;
    border-radius: 28px;
    overflow: hidden;
  }
  .card-front { top: 139px; background: var(--navy); }
  .card-back { top: 646px; background: var(--paper); }

  .front-brand {
    position: absolute;
    top: 168px;
    left: 20px;
    width: 100%;
    text-align: center;
    color: var(--paper);
    font-weight: 500;
    font-size: 76px;
    letter-spacing: -1px;
    line-height: 1;
  }
  .front-licences {
    position: absolute;
    top: 255px;
    left: 20px;
    width: 100%;
    text-align: center;
    color: var(--paper);
    font-size: 17px;
    line-height: 20px;
    letter-spacing: 1px;
  }
  .front-licences .divider { color: var(--sky); margin: 0 12px; }

  .edge-strip { position: absolute; left: 0; width: 15px; background: var(--navy); }
  .edge-strip.upper { top: 0; height: 171px; border-bottom-right-radius: 8px; }
  .edge-strip.lower { top: 237px; bottom: 0; border-top-right-radius: 8px; }
  .edge-tab {
    position: absolute; left: 0; top: 183px; width: 15px; height: 48px;
    background: var(--sky); border-radius: 0 8px 8px 0;
  }

  .back-brand {
    position: absolute;
    top: 82px;
    right: 38px;
    color: var(--navy);
    font-weight: 500;
    font-size: 44px;
    letter-spacing: -0.5px;
    line-height: 1;
  }
  .holder { position: absolute; left: 37px; top: 178px; }
  .holder-name {
    color: var(--sky);
    font-weight: 600;
    font-size: 28px;
    letter-spacing: 0.5px;
    line-height: 1;
  }
  .holder-title { color: var(--ink); font-size: 18px; margin-top: 8px; }

  .address {
    position: absolute; left: 429px; top: 178px;
    font-style: normal;
    color: var(--ink); font-size: 18px; line-height: 28px; letter-spacing: 0.2px;
  }
  .contacts { position: absolute; left: 429px; top: 284px; list-style: none; }
  .contacts li {
    display: flex; align-items: center; gap: 8px;
    color: var(--ink); font-size: 18px; line-height: 28px; letter-spacing: 0;
  }
  .contacts svg { width: 16px; height: 16px; fill: var(--sky); flex: none; }
</style>
</head>
<body>
  <section class="card card-front">
    <div class="front-brand">HearthMile</div>
    <p class="front-licences">NMLS 61947<span class="divider">|</span>Company NMLS 274615</p>
  </section>

  <section class="card card-back">
    <div class="edge-strip upper"></div>
    <div class="edge-tab"></div>
    <div class="edge-strip lower"></div>

    <div class="back-brand">HearthMile</div>

    <div class="holder">
      <h1 class="holder-name">MARCUS PELL</h1>
      <p class="holder-title">CEO</p>
    </div>

    <address class="address">
      48 Birchwell Court, Suite 314<br>
      Farrow Bend, OR 97512
    </address>

    <ul class="contacts">
      <li>
        <svg viewBox="0 0 16 16" aria-hidden="true"><path d="M3.5 1.5l2.2 2.6-1.3 1.6c.9 1.9 2.2 3.2 4 4.1l1.6-1.3 2.6 2.2-1.2 2.4C6.5 13 3 9.5 1.2 2.7z"/></svg>
        541-555-0182
      </li>
      <li>
        <svg viewBox="0 0 16 16" aria-hidden="true"><path d="M1 4h14v1.2L8 9.4 1 5.2z"/><path d="M1 6.6l7 4.2 7-4.2V13H1z"/></svg>
        email@hearthmile.example
      </li>
      <li>
        <svg viewBox="0 0 16 16" aria-hidden="true"><circle cx="8" cy="8" r="7"/><path d="M4 5c1.5 0 2 1 3 1s1 1.5 0 2-1 2-2.5 2.5C4 9 3 7 4 5zM10 3c1 1 2.5 1 3 3-1 0-2 .5-2.5 2-.5-1-1.5-1-1.5-2.5S10 4 10 3z" fill="#fff"/></svg>
        www.hearthmile.example
      </li>
    </ul>
  </section>
</body>
</html>
```